New Business Cards for Tormin Group

We need a new Business Card to compliment our new logo. We are a vibrant design, manufacture and install business providing recreation areas, public parks and Municipal spaces. We want business cards that are classy, modern and clean.

We have recently changed our logo, and are celebrating our 40th anniversary. We want business cards with a new modern design to reflect our status.

Target Market(s)

Customers

Contact Information for Business Card

We need all the details of our 3 offices as per the business card attached. Please disregard the old logo on the business card, the other three files show our new logo.

Requirements
Must have
• All info as per attached business card but with new logo.
Nice to have

```html
<!DOCTYPE html>
<html lang="en">
<head>
<meta charset="utf-8">
<title>Tormin Group Business Card</title>
<link href="https://fonts.googleapis.com/css2?family=Lato:wght@400;700&family=Roboto:wght@400;700&display=swap" rel="stylesheet">
<style>
  :root {
    --backdrop: #34343a;
    --card: #1e1f22;
    --red: #e8262d;
    --grey: #8a8b90;
    --light: #f2f2f2;
    --rule: #55565b;
  }
  * { margin: 0; padding: 0; box-sizing: border-box; }
  html, body { width: 1200px; height: 1108px; overflow: hidden; background: var(--backdrop); }
  .stage { position: relative; width: 1200px; height: 1108px; }
  .card {
    position: absolute; top: 214px; width: 420px; height: 680px;
    background: var(--card); border-radius: 24px;
  }
  .card--front { left: 150px; font-family: 'Lato', sans-serif; text-align: center; }
  .card--back { left: 630px; font-family: 'Roboto', sans-serif; text-align: center; }

  .brand { position: absolute; top: 190px; left: 0; right: 0;
    display: flex; align-items: center; justify-content: center; gap: 14px; }
  .brand__dot { width: 30px; height: 30px; border-radius: 50%; background: var(--red); }
  .brand__name { font-family: 'Lato', sans-serif; font-weight: 700; font-size: 40px;
    letter-spacing: 2px; color: var(--red); }

  .person { position: absolute; top: 418px; left: 0; right: 0; }
  .person__name { color: var(--red); font-size: 27px; font-weight: 400; text-transform: uppercase; letter-spacing: 0.5px; }
  .person__role { color: var(--grey); font-size: 19px; margin-top: 2px; }
  .divider { display: flex; align-items: center; justify-content: center; gap: 8px; margin: 16px 46px 14px; }
  .divider__line { flex: 1; height: 1px; background: var(--rule); }
  .icon { width: 26px; height: 26px; border-radius: 50%; background: var(--red);
    display: flex; align-items: center; justify-content: center; }
  .contact { color: var(--grey); font-size: 19px; line-height: 27px; }

  .pattern { position: absolute; top: 0; left: 0; right: 0; height: 330px;
    border-radius: 24px 24px 0 0;
    background: linear-gradient(180deg, #26272b 0%, #222326 70%, var(--card) 100%); }
  .offices { position: absolute; top: 190px; left: 0; right: 0; }
  .office__title { color: var(--red); font-weight: 700; font-size: 24px; margin-bottom: 6px; }
  .office__line { color: var(--light); font-size: 18px; line-height: 24px; }
  .office__label { color: var(--red); font-weight: 700; }
  .office__rule { width: 190px; height: 1px; background: var(--rule); margin: 16px auto 16px; }
</style>
</head>
<body>
<main class="stage">
  <section class="card card--front">
    <div class="brand">
      <span class="brand__dot"></span>
      <span class="brand__name">TORMIN GROUP</span>
    </div>
    <div class="person">
      <h1 class="person__name">Sam Delavane</h1>
      <p class="person__role">Managing Partner</p>
      <div class="divider">
        <span class="divider__line"></span>
        <span class="icon"><svg width="14" height="14" viewBox="0 0 24 24"><path fill="#1e1f22" d="M6.6 10.8a15 15 0 0 0 6.6 6.6l2.2-2.2c.3-.3.7-.4 1-.2 1.1.4 2.3.6 3.6.6.6 0 1 .4 1 1V20c0 .6-.4 1-1 1A17 17 0 0 1 3 4c0-.6.4-1 1-1h3.5c.6 0 1 .4 1 1 0 1.3.2 2.5.6 3.6.1.3 0 .7-.2 1z"/></svg></span>
        <span class="icon"><svg width="14" height="14" viewBox="0 0 24 24"><path fill="#1e1f22" d="M3 5h18v14H3z"/><path d="M3 5l9 8 9-8" fill="none" stroke="#e8262d" stroke-width="2"/></svg></span>
        <span class="icon"><svg width="14" height="14" viewBox="0 0 24 24"><circle cx="12" cy="12" r="9" fill="none" stroke="#1e1f22" stroke-width="2.4"/><path d="M3 12h18M12 3c3 3 3 15 0 18M12 3c-3 3-3 15 0 18" fill="none" stroke="#1e1f22" stroke-width="1.8"/></svg></span>
        <span class="divider__line"></span>
      </div>
      <p class="contact">+971 (0)50 318 7042<br>sam@tormingroup.com<br>www.tormingroup.com</p>
    </div>
  </section>

  <section class="card card--back">
    <div class="pattern" role="img" aria-label="Faint repeating company mark pattern"></div>
    <div class="offices">
      <div class="office">
        <h2 class="office__title">Head Office</h2>
        <p class="office__line">P.O.Box:41820 Abu Dhabi,U.A.E.</p>
        <p class="office__line"><span class="office__label">P :</span> +971 (0)2 5530917</p>
        <p class="office__line"><span class="office__label">F :</span> +971 (0)2 5530918</p>
        <p class="office__line"><span class="office__label">E :</span> sales@tormingroup.com</p>
      </div>
      <div class="office__rule"></div>
      <div class="office">
        <h2 class="office__title">Dubai Office</h2>
        <p class="office__line">P.O.Box:270436 Dubai,U.A.E.</p>
        <p class="office__line"><span class="office__label">P :</span> +971 (0)4 3867254</p>
        <p class="office__line"><span class="office__label">F :</span> +971 (0)2 3867255</p>
        <p class="office__line"><span class="office__label">E :</span> sales@tormingroup.com</p>
      </div>
      <div class="office__rule"></div>
      <div class="office">
        <h2 class="office__title">Qatar Office</h2>
        <p class="office__line">P.O.Box:30972 Doha, Qatar</p>
        <p class="office__line"><span class="office__label">P :</span> +974 44710386</p>
        <p class="office__line"><span class="office__label">F :</span> +971 44710387</p>
        <p class="office__line"><span class="office__label">E :</span> sales@tormingroup.com</p>
      </div>
    </div>
  </section>
</main>
</body>
</html>
```